Front and content page design for Fitness Cookbook

I am looking for someone to Design a front cover for a Recipe book and also create an amazing layout for the book.

Its for a corporate seminar so has to be eye catching, professional and bold.

Content is complete

Target Market(s)

Industry/Entity Type

Health And Wellness

Font styles to use
Sans Serif

Requirements
Must have
• Eye catching, professional and bold.
• By Dorian as stated on the document
• Must have Tidewell Motion Logo on it.

```html
<!DOCTYPE html>
<html lang="en">
<head>
<meta charset="utf-8">
<title>Spiced Cauliflower Sauté</title>
<link rel="stylesheet" href="https://fonts.googleapis.com/css2?family=Cabin:wght@400;500;600&display=swap">
<style>
  :root {
    --page: #ffffff;
    --accent: #f7941d;
    --ink: #2b2b2b;
    --title: #ffffff;
    --photo-top: #d9d3c6;
    --photo-mid: #c9a27a;
    --photo-low: #e07a32;
  }
  html, body {
    margin: 0;
    padding: 0;
    overflow: hidden;
    background: var(--page);
  }
  .page {
    position: relative;
    width: 849px;
    height: 1200px;
    overflow: hidden;
    background: var(--page);
    font-family: "Cabin", "Helvetica Neue", Arial, sans-serif;
    color: var(--ink);
  }
  .dish-photo {
    position: absolute;
    left: 28px;
    top: 22px;
    width: 793px;
    height: 468px;
    background:
      radial-gradient(ellipse at 50% 45%, var(--photo-mid) 0%, rgba(201,162,122,0.6) 40%, rgba(217,211,198,0) 75%),
      linear-gradient(180deg, var(--photo-top) 0%, #e6e1d7 60%, #cfc6b5 100%);
  }
  .title-band {
    position: absolute;
    left: 0;
    top: 506px;
    width: 849px;
    height: 172px;
    background: var(--accent);
    display: flex;
    align-items: center;
    justify-content: center;
  }
  .recipe-title {
    margin: 0;
    color: var(--title);
    font-weight: 400;
    font-size: 58px;
    letter-spacing: 0.5px;
  }
  .recipe-body {
    position: absolute;
    left: 52px;
    top: 720px;
    width: 745px;
  }
  .meta-line {
    margin: 0;
    font-size: 19px;
    line-height: 1.25;
  }
  .meta-label {
    color: var(--accent);
    font-weight: 500;
    text-transform: uppercase;
  }
  .section-heading {
    margin: 26px 0 4px;
    color: var(--accent);
    font-weight: 500;
    font-size: 19px;
    text-transform: uppercase;
  }
  .ingredient-list {
    list-style: none;
    margin: 0;
    padding: 0;
    font-size: 15.5px;
    line-height: 1.3;
  }
  .instructions-heading {
    margin: 26px 0 4px 8px;
  }
  .instructions-text {
    margin: 0;
    font-size: 15.5px;
    line-height: 1.35;
  }
  .page-footer {
    position: absolute;
    left: 42px;
    top: 1160px;
    display: flex;
    align-items: center;
    gap: 10px;
    font-size: 15px;
    color: var(--ink);
  }
  .brand-mark {
    display: flex;
    align-items: center;
    gap: 5px;
    color: var(--accent);
    font-weight: 500;
  }
  .brand-dot {
    width: 12px;
    height: 12px;
    border-radius: 50%;
    background: var(--accent);
  }
</style>
</head>
<body>
<main class="page">
  <div class="dish-photo" role="img" aria-label="Plated spiced cauliflower florets with sliced carrots and green peas"></div>

  <header class="title-band">
    <h1 class="recipe-title">Spiced Cauliflower Sauté</h1>
  </header>

  <section class="recipe-body">
    <p class="meta-line"><span class="meta-label">Prep time</span> 5 mins</p>
    <p class="meta-line"><span class="meta-label">Cooking time</span> 10 mins</p>

    <h2 class="section-heading">Ingredients</h2>
    <ul class="ingredient-list">
      <li>3 cups cauliflower</li>
      <li>1 whole carrot sliced</li>
      <li>1/3 cup peas</li>
      <li>1/4 cup water</li>
      <li>2 tsp ground cinnamon</li>
      <li>1 tbsp extra virgin olive oil</li>
    </ul>

    <h2 class="section-heading instructions-heading">Cooking instructions</h2>
    <p class="instructions-text">In a frying pan add the cauliflower and sliced carrot and the 1/4 cup of water on a medium heat. Once the water has almost evaporated add the peas and cook till cauliflower is slightly brown. Add the cinnamon for the last minute and stir. Remove and cool down for 2 mins before stirring in the olive oil.</p>
  </section>

  <footer class="page-footer">
    <span class="page-number">18</span>
    <span class="brand-mark"><span class="brand-dot"></span>Tidewell Motion</span>
  </footer>
</main>
</body>
</html>
```